Forensic Document Examiner, looking for contemporary update to my stationery design.

Looking for professional, classy logo design for stationery and business cards. My current stationery and business card is attached.I believe a logo image makes a header section interesting, so an intriguing design of a pen, feathered pen, microscope, magnifying glass, etc., would be appropriate. I have been in the business for over 30 years. I leave ideas to the imagination of the designer.My work involves mainly, the comparison of signatures and handwriting. I also resolve alterations, obliterations, and work as shown on my website: www.documentexaminer.infoThe image produced will be printed on quality white stationery and envelopes. The stationery will be photocopied by my clients, so the images should be reproducible. The business cards may be designed in other than white.

Target Market(s)

Attorneys

Font styles to use
Sans Serif

Colors

Designer to choose colors to be used in the design.

Requirements
Must have
• Image suitable for white stationery and photocopying.
• Classy logo and image; no casual fonts.
Nice to have
• Intriguing, contemporary design incorporating a relevant logo to my work.

```html
<!DOCTYPE html>
<html lang="en">
<head>
<meta charset="utf-8">
<title>Daniel R. Whitmore – Forensic Document Examiner</title>
<link rel="stylesheet" href="https://fonts.googleapis.com/css2?family=Lato:ital,wght@0,700;1,400;1,700&display=swap">
<style>
  :root {
    --backdrop: #b9b9b9;
    --paper: #f1f1f1;
    --navy: #27286b;
    --band-top: #4a4690;
    --band-bottom: #2c2a6c;
    --grey-text: #7a7a7a;
    --mark-grey: #c6c7cb;
    --white: #ffffff;
  }
  html, body {
    margin: 0;
    padding: 0;
    width: 1157px;
    height: 1200px;
    overflow: hidden;
    background: var(--backdrop);
  }
  .cover {
    position: absolute;
    left: 255px;
    top: 78px;
    width: 646px;
    height: 1044px;
    background: var(--paper);
    overflow: hidden;
  }
  .cover-art {
    position: absolute;
    inset: 0;
  }
  .identity {
    position: absolute;
    left: 65px;
    top: 512px;
    display: flex;
    align-items: center;
    gap: 24px;
  }
  .identity-mark {
    width: 72px;
    height: 72px;
    border-radius: 50%;
    background: var(--mark-grey);
    flex: none;
  }
  .identity-name {
    margin: 0;
    font-family: "Lato", sans-serif;
    font-weight: 700;
    font-size: 42px;
    line-height: 1;
    color: var(--navy);
  }
  .identity-role {
    margin: 12px 0 0;
    font-family: "Lato", sans-serif;
    font-style: italic;
    font-weight: 400;
    font-size: 24px;
    letter-spacing: 0.5px;
    color: var(--grey-text);
  }
  .footer-band {
    position: absolute;
    left: 0;
    bottom: 0;
    width: 100%;
    height: 50px;
    background: linear-gradient(var(--band-top), var(--band-bottom));
    display: flex;
    align-items: center;
    justify-content: center;
  }
  .footer-url {
    font-family: "Lato", sans-serif;
    font-style: italic;
    font-weight: 700;
    font-size: 17px;
    color: var(--white);
    letter-spacing: 0.3px;
  }
</style>
</head>
<body>
  <main class="cover">
    <svg class="cover-art" width="646" height="1044" viewBox="0 0 646 1044" xmlns="http://www.w3.org/2000/svg">
      <defs>
        <linearGradient id="documentFade" x1="0" y1="0" x2="0" y2="1">
          <stop offset="0" stop-color="#d8d8d8"/>
          <stop offset="1" stop-color="#f1f1f1"/>
        </linearGradient>
        <linearGradient id="courtroomTone" x1="0" y1="0" x2="1" y2="1">
          <stop offset="0" stop-color="#e8d6b4"/>
          <stop offset="0.45" stop-color="#c49a5c"/>
          <stop offset="1" stop-color="#7c5a2e"/>
        </linearGradient>
        <linearGradient id="silverEdge" x1="0" y1="1" x2="1" y2="0">
          <stop offset="0" stop-color="#c9cbd0"/>
          <stop offset="0.5" stop-color="#f4f4f6"/>
          <stop offset="1" stop-color="#b4b6bc"/>
        </linearGradient>
      </defs>

      <rect class="document-photo" role="img" aria-label="Faded photograph of reading glasses resting on a last will document"
            x="0" y="0" width="646" height="192" fill="url(#documentFade)"/>

      <path class="courtroom-photo" role="img" aria-label="Photograph of a judge raising a gavel in a courtroom beside a flag"
            d="M0 992 C 80 850 190 790 370 750 C 520 716 620 680 646 544 L646 1044 L0 1044 Z"
            fill="url(#courtroomTone)"/>

      <path class="wave-edge" d="M0 992 C 80 850 190 790 370 750 C 520 716 620 680 646 544"
            fill="none" stroke="url(#silverEdge)" stroke-width="13"/>
      <path class="wave-edge-line" d="M0 981 C 80 839 190 780 370 740 C 520 706 615 670 646 533"
            fill="none" stroke="#d9dade" stroke-width="3"/>
    </svg>

    <div class="identity">
      <div class="identity-mark"></div>
      <div>
        <h1 class="identity-name">Daniel R. Whitmore</h1>
        <p class="identity-role">Forensic Document Examiner</p>
      </div>
    </div>

    <footer class="footer-band">
      <span class="footer-url">www.quillmarkreview.info</span>
    </footer>
  </main>
</body>
</html>
```